Business card for Eyelash extension salon in Beverly Hills,California USA

We need new business card for our salon in Beverly Hills. The salon name is 'Lashvera' . We would like to have...Business name: Lashvera Name of person: will provide later Address 4720 N.Alder Crest Ave Beverly Hills , CA 90210 Phone: will provide later (Text only) Web: www.lashverastudio.example Snapgrid icon, Circlebook icon follow us for seasonal campaign and news @lashverastudiolounge Design should look elegant, high-end, clean, simple, cohesive with my brand. Please refer my brand board. Business name color will be metallic bronzy color. Im thinking grey background or white background. Thanks

Target Market(s)

25-35. Gender neutral. People who are in Entertainment business industry.
This is High-end Eyelash extension salon in Beverly Hills

Industry/Entity Type

Beauty Salon

Contact Information for Business Card

Business name: Lashvera
Name of person: will provide later
Address 4720 N.Alder Crest Ave Beverly Hills , CA 90210
Phone: will provide later (Text only)
Web: www.lashverastudio.example
Snapgrid icon, Circlebook icon
follow us for seasonal campaign and news @lashverastudiolounge

Requirements
Must have
• Beautiful, elegant, clean and simple look but very attractive and modern
Should not have
• We don't like too clutter, too busy designs.

```html
<!DOCTYPE html>
<html lang="en">
<head>
<meta charset="utf-8">
<title>Lashvera Business Card</title>
<link href="https://fonts.googleapis.com/css2?family=Lato:wght@300;400;700&display=swap" rel="stylesheet">
<style>
  :root {
    --bronze: #8a6a50;
    --bronze-card: #8b6a4f;
    --ink: #2b2b2b;
    --paper: #ffffff;
    --backdrop: #2c2c2c;
    --divider-light: #d9d2cc;
    --divider-dark: #a48a74;
  }
  * { margin: 0; padding: 0; box-sizing: border-box; }
  html, body {
    width: 1200px; height: 802px; overflow: hidden;
    background: var(--backdrop);
    font-family: "Lato", Arial, sans-serif;
  }
  .stage { position: relative; width: 1200px; height: 802px; }
  .card {
    position: absolute; top: 274px; width: 442px; height: 265px;
  }
  .card--front { left: 136px; background: var(--paper); }
  .card--back { left: 624px; background: var(--bronze-card); }

  .brand {
    position: absolute; left: 30px; top: 92px; width: 170px;
    text-align: center;
  }
  .brand__name {
    font-family: "Lato", Arial, sans-serif;
    font-weight: 300; font-size: 38px; letter-spacing: 1px; line-height: 1;
  }
  .brand__place {
    margin-top: 8px; font-size: 6.5px; letter-spacing: 1.6px;
    font-weight: 400; text-transform: uppercase;
  }
  .card--front .brand__name, .card--front .brand__place { color: var(--bronze); }
  .card--back .brand__name, .card--back .brand__place { color: var(--paper); }

  .divider { position: absolute; left: 225px; top: 78px; width: 1px; height: 114px; }
  .card--front .divider { background: var(--divider-light); }
  .card--back .divider { background: var(--divider-dark); left: 215px; }

  .contact { position: absolute; left: 243px; top: 90px; color: var(--ink); }
  .contact__name {
    font-family: Arial, "Lato", sans-serif; font-weight: 700;
    font-size: 16px; color: var(--bronze); letter-spacing: 0.3px;
    margin-bottom: 10px;
  }
  .contact__line { font-size: 12px; line-height: 15.5px; }
  .contact__group { margin-bottom: 5px; }
  .contact__row { display: flex; align-items: center; gap: 4px; }
  .contact__row svg { width: 10px; height: 10px; flex: none; }

  .social { position: absolute; left: 236px; top: 96px; color: var(--paper); }
  .social__links { display: flex; gap: 10px; margin-bottom: 8px; font-size: 10px; }
  .social__link { display: flex; align-items: center; gap: 4px; }
  .social__dot { width: 9px; height: 9px; border-radius: 50%; background: var(--paper); }
  .social__text {
    font-family: Arial, "Lato", sans-serif; font-size: 12.8px; line-height: 16px;
  }
  .social__handle { font-weight: 700; }
</style>
</head>
<body>
<main class="stage">
  <section class="card card--front" aria-label="Business card front">
    <div class="brand">
      <div class="brand__name">Lashvera</div>
      <div class="brand__place">Beverly Hills</div>
    </div>
    <div class="divider"></div>
    <div class="contact">
      <div class="contact__name">DANIEL MARSH</div>
      <div class="contact__group">
        <div class="contact__line">4720 N.Alder Crest Ave</div>
        <div class="contact__line">Beverly Hills , CA 90210</div>
      </div>
      <div class="contact__line contact__row">
        <svg viewBox="0 0 10 10" aria-hidden="true"><path d="M1 3.5 Q5 0.5 9 3.5 L8 5 L6.5 4 L6.5 3 Q5 2.5 3.5 3 L3.5 4 L2 5 Z M2.5 5.5 H7.5 L8.5 9 H1.5 Z" fill="#2b2b2b"/></svg>
        044-321 654 987
      </div>
      <div class="contact__line contact__row">
        <svg viewBox="0 0 10 10" aria-hidden="true"><circle cx="5" cy="5" r="4.3" fill="#2b2b2b"/><path d="M1 5 H9 M5 0.7 Q2.5 5 5 9.3 M5 0.7 Q7.5 5 5 9.3" stroke="#fff" stroke-width="0.7" fill="none"/></svg>
        www.lashverastudio.example
      </div>
    </div>
  </section>

  <section class="card card--back" aria-label="Business card back">
    <div class="brand">
      <div class="brand__name">Lashvera</div>
      <div class="brand__place">Beverly Hills</div>
    </div>
    <div class="divider"></div>
    <div class="social">
      <div class="social__links">
        <span class="social__link"><span class="social__dot"></span>Circlebook</span>
        <span class="social__link"><span class="social__dot"></span>Snapgrid</span>
      </div>
      <p class="social__text">Follow us<br>for seasonal campaign<br>and news <span class="social__handle">@lashverastudiolounge</span></p>
    </div>
  </section>
</main>
</body>
</html>
```